Business Card for a Dental Office

The design should communicate integrity, quality and reliability. We also want the card look elegant, simple, but still stand out, different from the traditional-dental-office business card.

Industry/Entity Type

Business

```html
<!DOCTYPE html>
<html lang="en">
<head>
<meta charset="utf-8">
<title>Harlow Dental Studio – Business Card</title>
<link rel="stylesheet" href="https://fonts.googleapis.com/css2?family=Oswald:wght@500&family=Open+Sans:wght@400;600&display=swap">
<style>
  :root {
    --backdrop: #5b5b5b;
    --card-black: #050505;
    --card-white: #ffffff;
    --gold: #e2c21a;
    --gold-deep: #b8930d;
    --gold-light: #f3e03a;
    --ink: #111111;
    --text-light: #ffffff;
  }
  * { box-sizing: border-box; margin: 0; padding: 0; }
  html, body {
    width: 1105px; height: 1200px; overflow: hidden;
    background: var(--backdrop);
  }
  .canvas { position: relative; width: 1105px; height: 1200px; }
  .card {
    position: absolute; left: 196px; width: 720px; height: 411px;
    overflow: hidden; background: var(--card-black);
  }
  .card--front { top: 146px; background: var(--card-white); }
  .card--back { top: 602px; }

  .front-curve { position: absolute; inset: 0; width: 720px; height: 411px; }

  .brand {
    position: absolute; left: 140px; top: 72px;
    display: flex; align-items: center; gap: 14px;
  }
  .brand__square { width: 64px; height: 64px; background: var(--ink); }
  .brand__text { display: flex; flex-direction: column; }
  .brand__name {
    font-family: "Oswald", sans-serif; font-weight: 500;
    font-size: 36px; line-height: 1; color: var(--ink); letter-spacing: 0.5px;
  }
  .brand__tagline {
    margin-top: 6px;
    font-family: "Open Sans", sans-serif; font-weight: 600;
    font-size: 14px; letter-spacing: 0.6px; color: var(--gold-deep);
    text-transform: uppercase;
  }

  .contact-person {
    position: absolute; left: 32px; top: 276px;
    font-family: "Open Sans", sans-serif; color: var(--text-light);
  }
  .contact-person__name { font-size: 25px; font-weight: 600; line-height: 34px; }
  .contact-person__line { font-size: 19px; line-height: 27px; }

  .contact-list {
    position: absolute; right: 30px; top: 276px; list-style: none;
    font-family: "Open Sans", sans-serif; color: var(--text-light);
    font-size: 19px; line-height: 27.5px; text-align: right;
  }
  .contact-list li { display: flex; justify-content: flex-end; align-items: center; gap: 10px; }
  .contact-list svg { width: 18px; height: 18px; fill: var(--text-light); }

  .back-block {
    position: absolute; left: 0; top: 60px; width: 340px; height: 351px;
    background: linear-gradient(135deg, var(--gold-light), var(--gold) 50%, var(--gold-deep));
  }
  .back-brand {
    position: absolute; left: 408px; top: 296px;
    font-family: "Oswald", sans-serif; color: var(--gold);
  }
  .back-brand__name { font-weight: 500; font-size: 29px; line-height: 1; }
  .back-brand__tagline {
    margin-top: 3px; font-family: "Open Sans", sans-serif; font-weight: 600;
    font-size: 11.5px; letter-spacing: 0.4px; text-transform: uppercase;
  }
  .back-brand__web {
    margin-top: 4px; font-family: "Open Sans", sans-serif;
    font-size: 17px; letter-spacing: 3.4px;
  }
</style>
</head>
<body>
<main class="canvas">
  <section class="card card--front">
    <svg class="front-curve" viewBox="0 0 720 411" aria-hidden="true">
      <path d="M0 190 Q360 318 720 190 L720 411 L0 411 Z" fill="#050505"/>
      <path d="M0 196 Q360 326 720 196" fill="none" stroke="#e2c21a" stroke-width="4"/>
      <path d="M0 192 Q360 262 720 192" fill="none" stroke="#050505" stroke-width="2"/>
    </svg>

    <div class="brand">
      <span class="brand__square"></span>
      <div class="brand__text">
        <span class="brand__name">HARLOW DENTAL STUDIO</span>
        <span class="brand__tagline">Gentle care you can trust for life</span>
      </div>
    </div>

    <div class="contact-person">
      <p class="contact-person__name">Alex Morgan</p>
      <p class="contact-person__line">CEO/Founder</p>
      <p class="contact-person__line">1420 Cedar Hollow Road</p>
      <p class="contact-person__line">Fairview, Oregon 97024</p>
    </div>

    <ul class="contact-list">
      <li>555 210 4417
        <svg viewBox="0 0 24 24"><path d="M6.6 10.8a15.1 15.1 0 0 0 6.6 6.6l2.2-2.2c.3-.3.7-.4 1-.2 1.1.4 2.3.6 3.6.6.6 0 1 .4 1 1V20c0 .6-.4 1-1 1A17 17 0 0 1 3 4c0-.6.4-1 1-1h3.5c.6 0 1 .4 1 1 0 1.3.2 2.5.6 3.6.1.3 0 .7-.2 1z"/></svg>
      </li>
      <li>555 380 6925
        <svg viewBox="0 0 24 24"><path d="M7 1h10a2 2 0 0 1 2 2v18a2 2 0 0 1-2 2H7a2 2 0 0 1-2-2V3a2 2 0 0 1 2-2zm0 3v15h10V4zm5 16.2a1 1 0 1 0 0 2 1 1 0 0 0 0-2z"/></svg>
      </li>
      <li>hello@harlowdental.com
        <svg viewBox="0 0 24 24"><path d="M2 5h20v14H2zm2 2v.4l8 5 8-5V7zm0 2.8V17h16V9.8l-8 5z"/></svg>
      </li>
      <li>www.harlowdental.com
        <svg viewBox="0 0 24 24"><path d="M12 2a10 10 0 1 0 0 20 10 10 0 0 0 0-20zm-1 17.9A8 8 0 0 1 4.2 10.2L9 15v1a2 2 0 0 0 2 2zm6.9-2.5A2 2 0 0 0 16 16h-1v-3a1 1 0 0 0-1-1H8v-2h2a1 1 0 0 0 1-1V7h2a2 2 0 0 0 2-2v-.4a8 8 0 0 1 2.9 12.8z"/></svg>
      </li>
    </ul>
  </section>

  <section class="card card--back">
    <div class="back-block"></div>
    <div class="back-brand">
      <p class="back-brand__name">HARLOW DENTAL STUDIO</p>
      <p class="back-brand__tagline">Gentle care you can trust for life</p>
      <p class="back-brand__web">www.harlowdental.com</p>
    </div>
  </section>
</main>
</body>
</html>
```